Design a WordPress layout for a home loans company

The home loans company in question is going through a rebrand and needs a new website layout.
Sites they like: http://www.brightkeylending.com.au/
Current logo: Attached.
Colours to be used: As per those used in logo.
Primary: #71aa3d
Secondary: #130e10
Pages to be designed:
- Homepage
- Internal services page
Menu items for display purposes:
- Home
- About Us
- Speak to a Broker
- Articles
- Contact Us
A modern design with simplicity is key.
For copy, dummy text such as Lorem ipsum will be fine.
If you would like anything elso, please ask.
Target Market(s)
25-40 year old
Mostly female
Buying their first home in most cases
Industry/Entity Type
Mortgage Brokerage
Number of Pages Required
2 page

```html
<!DOCTYPE html>
<html lang="en">
<head>
<meta charset="utf-8">
<title>Oakline Home Loans</title>
<link rel="stylesheet" href="https://fonts.googleapis.com/css2?family=Mulish:wght@400;700;800&family=Open+Sans:wght@400;600&display=swap">
<style>
:root{
  --green:#71aa3d;
  --green-dark:#5f9a2f;
  --ink:#130e10;
  --text:#333333;
  --muted:#555555;
  --line:#cfcfcf;
  --grey-band:#eeeeee;
  --footer:#2b2b2b;
  --white:#ffffff;
}
*{margin:0;padding:0;box-sizing:border-box}
html,body{width:1200px;height:2198px;overflow:hidden;background:var(--white)}
body{font-family:"Open Sans",Arial,sans-serif;color:var(--text);position:relative}
.wrap{position:absolute;inset:0}

/* header */
.site-header{position:absolute;left:0;top:0;width:1200px;height:133px}
.brand{position:absolute;left:133px;top:50px;display:flex;align-items:center;gap:10px;
  font-family:"Mulish",sans-serif;font-weight:800;font-size:30px;color:var(--green);letter-spacing:-.3px}
.brand-mark{width:14px;height:14px;background:var(--green)}
.search{position:absolute;left:645px;top:23px;width:263px;height:37px;border:1px solid var(--line);
  background:#f1f1f1;border-radius:3px;font-size:12px;color:#555;padding:10px 15px}
.search svg{position:absolute;right:12px;top:10px}
.quote-btn{position:absolute;left:917px;top:23px;width:151px;height:37px;background:var(--ink);color:var(--white);
  font-family:"Mulish",sans-serif;font-weight:700;font-size:13px;display:flex;align-items:center;justify-content:center;border-radius:3px}
.main-nav{position:absolute;right:132px;top:96px;display:flex;gap:33px;font-size:13.5px;color:#222}
.main-nav .active{color:var(--green)}

/* hero */
.hero{position:absolute;left:0;top:133px;width:1200px;height:481px;
  background:linear-gradient(100deg,#8b7a6a 0%,#c9bfb3 30%,#b6a795 55%,#d8d1c4 75%,#c4a35a 100%)}
.hero-caption{position:absolute;left:0;right:0;top:422px;text-align:center;font-family:"Mulish",sans-serif;
  font-weight:700;font-size:32px;color:var(--white);text-shadow:0 1px 3px rgba(0,0,0,.4)}
.hero-arrow{position:absolute;top:223px}
.hero-arrow.prev{left:43px}.hero-arrow.next{left:1120px}

/* welcome */
.welcome h1{position:absolute;left:133px;top:686px;font-family:"Mulish",sans-serif;font-weight:700;font-size:33px;color:var(--green)}
.welcome p{position:absolute;left:133px;top:737px;width:600px;font-size:13.6px;line-height:25.6px;color:#333}
.welcome-photo{position:absolute;left:756px;top:694px;width:312px;height:217px;
  background:linear-gradient(135deg,#d9d4cb 0%,#b79a74 45%,#6c5a48 100%)}

/* broker form */
.broker{position:absolute;left:0;top:992px;width:1200px;height:343px;
  background:linear-gradient(180deg,#4b5b3c 0%,#3d6a3a 35%,#3f7a2e 70%,#2f5a24 100%)}
.broker h2{position:absolute;left:0;right:0;top:68px;text-align:center;font-family:"Mulish",sans-serif;font-weight:700;font-size:34px;color:var(--white)}
.field{position:absolute;height:38px;background:var(--white);font-size:13px;color:#555;padding:10px 14px}
.f-name{left:198px;top:124px;width:259px}
.f-email{left:470px;top:124px;width:260px}
.f-city{left:743px;top:124px;width:258px}
.f-msg{left:198px;top:176px;width:803px}
.submit{position:absolute;left:558px;top:224px;width:82px;height:39px;background:var(--green);color:var(--white);
  font-family:"Mulish",sans-serif;font-weight:800;font-size:14px;display:flex;align-items:center;justify-content:center}

/* articles */
.articles h2{position:absolute;left:0;right:0;top:1406px;text-align:center;font-family:"Mulish",sans-serif;font-weight:700;font-size:33px;color:var(--green)}
.card{position:absolute;top:1462px;width:286px}
.card-photo{width:286px;height:185px}
.card h3{margin-top:13px;font-weight:400;font-size:17.5px;line-height:20px;color:#222}
.card p{margin-top:10px;font-size:10.5px;line-height:17.5px;color:#555}
.read-more{position:absolute;top:319px;left:0;width:104px;height:40px;border:1px solid #9a9a9a;font-size:11.5px;
  color:#333;display:flex;align-items:center;justify-content:center}
.c1{left:133px}.c2{left:457px}.c3{left:781px}
.c1 .card-photo{background:linear-gradient(135deg,#e6e4dc,#9aa08a 60%,#4d4a40)}
.c2 .card-photo{background:linear-gradient(135deg,#c7d0d6,#e7dfd4 55%,#b9a78e)}
.c3 .card-photo{background:linear-gradient(135deg,#2f5a92,#7a7d80 55%,#c3b8a8)}
.art-arrow{position:absolute;top:1541px}
.art-arrow.prev{left:55px}.art-arrow.next{left:1128px}

/* contact */
.contact{position:absolute;left:0;top:1902px;width:1200px;height:190px;background:var(--grey-band);text-align:center}
.contact h2{margin-top:45px;font-family:"Mulish",sans-serif;font-weight:700;font-size:33px;color:var(--green)}
.contact .addr{margin-top:8px;font-family:"Mulish",sans-serif;font-size:16px;color:#222}
.contact .lines{margin-top:8px;font-family:"Mulish",sans-serif;font-weight:700;font-size:16px;color:#111;
  display:flex;justify-content:center;align-items:center;gap:8px}
.contact svg{vertical-align:-2px;margin-right:4px}

/* footer */
.site-footer{position:absolute;left:0;top:2092px;width:1200px;height:106px;background:var(--footer);color:#cfcfcf}
.footer-links{position:absolute;left:133px;top:31px;font-size:11px}
.footer-links span{margin:0 8px;color:#999}
.copyright{position:absolute;left:133px;top:59px;font-size:11px;color:#bdbdbd}
.social{position:absolute;left:1010px;top:40px;display:flex;gap:4px}
.social i{display:block;width:26px;height:26px;border-radius:50%}
.social .s1{background:#3b5998}.social .s2{background:#1da1f2}
</style>
</head>
<body>
<div class="wrap">

<header class="site-header">
  <div class="brand"><span class="brand-mark"></span>Oakline Home Loans</div>
  <div class="search">Search
    <svg width="15" height="15" viewBox="0 0 16 16"><circle cx="6.5" cy="6.5" r="5" fill="none" stroke="#333" stroke-width="2"/><line x1="10.3" y1="10.3" x2="15" y2="15" stroke="#333" stroke-width="2.4"/></svg>
  </div>
  <div class="quote-btn">REQUEST A QUOTE</div>
  <nav class="main-nav">
    <span class="active">HOME</span><span>ABOUT US</span><span>SPEAK TO BROKER</span><span>ARTICLES</span><span>CONTACT US</span>
  </nav>
</header>

<section class="hero" role="img" aria-label="Young couple reviewing home loan documents with a broker in a bright living room">
  <svg class="hero-arrow prev" width="36" height="36" viewBox="0 0 36 36"><circle cx="18" cy="18" r="16" fill="#2c3a1c" stroke="#71aa3d" stroke-width="3"/><polyline points="21,11 14,18 21,25" fill="none" stroke="#71aa3d" stroke-width="3"/></svg>
  <svg class="hero-arrow next" width="36" height="36" viewBox="0 0 36 36"><circle cx="18" cy="18" r="16" fill="#2c3a1c" stroke="#71aa3d" stroke-width="3"/><polyline points="15,11 22,18 15,25" fill="none" stroke="#71aa3d" stroke-width="3"/></svg>
  <div class="hero-caption">Maecenas vel tortor accumsan quam varius</div>
</section>

<section class="welcome">
  <h1>Welcome to Oakline home loans</h1>
  <p>Aenean sed quam non sapien faucibus consequat vitae sit amet orci. Praesent quis risus mi. In mollis nulla in pulvinar dictum. Vivamus interdum sagittis felis, ut dapibus ligula feugiat ac. In dictum sapien eu tellus finibus fermentum. Aenean faucibus lacus ut mollis commodo. Donec vestibulum odio sem, ac laoreet massa ullamcorper id. Donec molestie nisi et tellus hendrerit vehicula. Nunc eu ligula sed quam pulvinar maximus in vitae eros. Proin porta fermentum ipsum, vel porttitor turpis venenatis luctus. Vivamus volutpat eu sapien quis tempus. Aenean feugiat viverra lorem ac sagittis. Donec sit amet lectus nec mi tempor laoreet ac nec nunc.</p>
  <div class="welcome-photo" role="img" aria-label="Desk with laptop, calculator and paperwork for loan planning"></div>
</section>

<section class="broker" role="img" aria-label="Aerial view of homes beside a lake and golf course">
  <h2>Speak to Broker</h2>
  <div class="field f-name">Name</div>
  <div class="field f-email">Email</div>
  <div class="field f-city">City</div>
  <div class="field f-msg">Message</div>
  <div class="submit">SUBMIT</div>
</section>

<section class="articles">
  <h2>Articles</h2>
  <svg class="art-arrow prev" width="16" height="26" viewBox="0 0 16 26"><polyline points="13,2 3,13 13,24" fill="none" stroke="#777" stroke-width="2.5"/></svg>
  <svg class="art-arrow next" width="16" height="26" viewBox="0 0 16 26"><polyline points="3,2 13,13 3,24" fill="none" stroke="#777" stroke-width="2.5"/></svg>
  <article class="card c1">
    <div class="card-photo" role="img" aria-label="Architect reviewing house plans on a laptop beside a small model home"></div>
    <h3>Praesent elementum nulla sit amet justo pellentesque scelerisque.</h3>
    <p>Sed tellus ex, imperdiet eget gravida sit amet, volutpat eget turpis. In nec ultricies est. Etiam mattis augue vehicula odio posuere, sit amet tempus lectus luctus.</p>
    <div class="read-more">READ MORE</div>
  </article>
  <article class="card c2">
    <div class="card-photo" role="img" aria-label="Happy couple outside their new house"></div>
    <h3>Pellentesque convallis molestie enim sit amet efficitu</h3>
    <p>Sed tellus ex, imperdiet eget gravida sit amet, volutpat eget turpis. In nec ultricies est. Etiam mattis augue vehicula odio posuere, sit amet tempus lectus luctus.</p>
    <div class="read-more">READ MORE</div>
  </article>
  <article class="card c3">
    <div class="card-photo" role="img" aria-label="Broker meeting a client in an office with a home loans sign"></div>
    <h3>Fusce vitae lectus sit amet mi pulvinar maximus</h3>
    <p>Sed tellus ex, imperdiet eget gravida sit amet, volutpat eget turpis. In nec ultricies est. Etiam mattis augue vehicula odio posuere, sit amet tempus lectus luctus.</p>
    <div class="read-more">READ MORE</div>
  </article>
</section>

<section class="contact">
  <h2>Contact Us</h2>
  <div class="addr"><svg width="10" height="14" viewBox="0 0 10 14"><path d="M5 0a5 5 0 0 0-5 5c0 4 5 9 5 9s5-5 5-9a5 5 0 0 0-5-5z" fill="#222"/><circle cx="5" cy="5" r="2" fill="#eee"/></svg>24 Building name, Street name, City Zipcode</div>
  <div class="lines">
    <span><svg width="13" height="13" viewBox="0 0 16 16"><path d="M3.6 1l2.6 3.2-1.6 2a10 10 0 0 0 5.2 5.2l2-1.6L15 12.4 13.4 15C6.8 15 1 9.2 1 2.6z" fill="#111"/></svg>Phone : 555 204 7731</span>
    <span>&nbsp;/&nbsp;</span>
    <span><svg width="15" height="12" viewBox="0 0 15 12"><rect width="15" height="12" rx="1" fill="#111"/><polyline points="1,1.5 7.5,7 14,1.5" fill="none" stroke="#eee" stroke-width="1.4"/></svg>Email : info@oaklinehomeloans.com</span>
  </div>
</section>

<footer class="site-footer">
  <div class="footer-links">Home<span>|</span>About us<span>|</span>Speak to Broker<span>|</span>Articles<span>|</span>Contact us</div>
  <div class="copyright">Copyright &copy; 2018 Oakline home loans.&nbsp;&nbsp; All rights reserved.</div>
  <div class="social"><i class="s1"></i><i class="s2"></i></div>
</footer>

</div>
</body>
</html>
```